Vibrant, yet professional, stationery set and other designs required.

I need to source a fantastic designer for a new project as part of my company using a new logo designed via sketch harbor.

**UPDATE** I am not looking for just 'fine' design that will suffice. I am looking for something great.

We are a life assurance brokerage based in Dublin, Ireland and BrightRoost.ie is our new website aimed at providing services for young families in Ireland. We are hoping to be the 'Velro' level of service providers in this area and I am looking for the quality of design to reflect this :-) Hopefully that makes sense!

I have a preference for straight lines over curves and waves.

I need...

1. Business card
2. Letterhead
3. Banner (for printing - 76cm X 305cm)
4. Car branding for KORVA 9 (2014 sport model) I believe the templates are freely available online.

Target Market(s)

Parents in Ireland - Aged 27 to 50.

Industry/Entity Type

Financial Planning

Colors

Designer to choose colors to be used in the design.

Requirements
Must have
• All of the items listed in the description above. I like clean, bright, legible, vibrant and professional design.
Should not have
• No silly or 'cheap' looking designs. This is a professional company looking to provide a professional service.

```html
<!DOCTYPE html>
<html lang="en">
<head>
<meta charset="utf-8">
<title>BrightRoost.ie – Business Card</title>
<link rel="stylesheet" href="https://fonts.googleapis.com/css2?family=Open+Sans:wght@400;600;700&display=swap">
<style>
  :root {
    --backdrop: #ece9e4;
    --card-white: #ffffff;
    --slate: #7b9198;
    --slate-dark: #5f7379;
    --sky: #35bde6;
    --leaf: #8cc31a;
    --tangerine: #ff6c00;
    --ink: #4a4f52;
  }
  * { box-sizing: border-box; margin: 0; padding: 0; }
  html, body {
    width: 1200px; height: 800px; overflow: hidden;
    background: var(--backdrop);
    font-family: "Open Sans", Arial, sans-serif;
  }
  .stage {
    position: relative; width: 1200px; height: 800px;
  }
  .card {
    position: absolute; top: 257px;
    width: 500px; height: 286px;
    border-radius: 3px;
    box-shadow: 0 2px 10px rgba(0,0,0,0.12);
  }
  .card--front { left: 70px; background: var(--card-white); }
  .card--back  { left: 630px; background: var(--slate); }

  .brand-name {
    position: absolute; top: 38px; right: 36px;
    font-weight: 700; font-size: 34px; letter-spacing: -0.5px;
    color: var(--slate);
    display: flex; align-items: center; gap: 10px;
  }
  .brand-dot {
    width: 14px; height: 14px; border-radius: 50%;
    background: var(--tangerine);
  }

  .contact {
    position: absolute; left: 36px; bottom: 30px;
    color: var(--ink); font-size: 13px; line-height: 17px;
  }
  .contact__name { color: var(--sky); font-weight: 600; font-size: 16px; line-height: 19px; text-transform: uppercase; }
  .contact__role { color: var(--leaf); font-weight: 600; font-size: 15px; line-height: 18px; text-transform: uppercase; margin-bottom: 4px; }
  .contact__address { margin-bottom: 4px; }
  .contact__list { list-style: none; }
  .contact__list li { display: flex; align-items: center; gap: 8px; }
  .contact__list svg { width: 11px; height: 11px; fill: var(--sky); flex: none; }

  .back-brand {
    position: absolute; inset: 0;
    display: flex; align-items: center; justify-content: center; gap: 12px;
    font-weight: 700; font-size: 36px; color: var(--card-white);
  }
  .back-brand .brand-dot { width: 18px; height: 18px; background: var(--leaf); }
</style>
</head>
<body>
<main class="stage">
  <section class="card card--front">
    <div class="brand-name"><span class="brand-dot"></span>BrightRoost.ie</div>
    <div class="contact">
      <p class="contact__name">Niamh Carroll</p>
      <p class="contact__role">CEO/Founder</p>
      <p class="contact__address">14 Harcourt Row<br>Dublin 2, D02 K318</p>
      <ul class="contact__list">
        <li><svg viewBox="0 0 12 12"><path d="M1 4c0-2 2-3 5-3s5 1 5 3v1H8V4H4v1H1zM2 6h8l1 5H1z"/></svg>01 482 7730</li>
        <li><svg viewBox="0 0 12 12"><path d="M3 0h6v12H3zM4 1.5v8h4v-8z"/></svg>087 315 6624</li>
        <li><svg viewBox="0 0 12 12"><path d="M3 0h6v3H3zM0 4h12v5H10v3H2V9H0zM3 8v3h6V8z"/></svg>01 482 7731</li>
        <li><svg viewBox="0 0 12 12"><path d="M0 2h12v8H0zM1 3l5 4 5-4z" fill-rule="evenodd"/></svg>hello@brightroost.ie</li>
        <li><svg viewBox="0 0 12 12"><circle cx="6" cy="6" r="6"/></svg>www.brightroost.ie</li>
      </ul>
    </div>
  </section>

  <section class="card card--back">
    <div class="back-brand"><span class="brand-dot"></span>BrightRoost.ie</div>
  </section>
</main>
</body>
</html>
```